Maple Roster Business Card for recruitment company

We are looking for a Business Card Design that incorporates our personal details and our busines name and logo. We are a specialized search consultancy that recruit Property and Construction professionals.
We would like a business card that stands out and is appealing to the Construction and Property industry as well.

Target Market(s)

people in the construction and property industry

Contact Information for Business Card

Business Name and logo

Font styles to use
Serif

Colors
0094D4
00A9DD
6FCCEA
C7EBF8
E9F6FB

Requirements
Must have
• Business name and logo as well as contact details
Should not have
• No photos of us please

```html
<!DOCTYPE html>
<html lang="en">
<head>
<meta charset="utf-8">
<title>Maple Roster Business Card</title>
<link href="https://fonts.googleapis.com/css2?family=Lora:wght@400;700&display=swap" rel="stylesheet">
<style>
  :root {
    --page: #e9ecef;
    --teal: #0b4259;
    --teal-deep: #08364a;
    --blue: #0a8fc6;
    --white: #ffffff;
  }
  * { margin: 0; padding: 0; box-sizing: border-box; }
  html, body { width: 1200px; height: 912px; overflow: hidden; }
  body {
    position: relative;
    background: var(--page);
    font-family: "Lora", Georgia, serif;
  }
  .card {
    position: absolute;
    width: 620px;
    height: 354px;
    overflow: hidden;
    box-shadow: 0 10px 28px rgba(0,0,0,.22);
  }

  /* Back side */
  .card-back { left: 80px; top: 60px; background: var(--teal); }
  .card-back .pattern-area {
    position: absolute; inset: 0;
    background: linear-gradient(200deg, var(--blue) 0%, #0a6f9c 30%, var(--teal) 62%, var(--teal-deep) 100%);
  }
  .back-brand {
    position: absolute; right: 34px; top: 142px;
    display: flex; align-items: center; gap: 10px;
    color: var(--white); font-size: 22px; letter-spacing: 2px;
    text-transform: uppercase;
  }
  .brand-dot {
    display: inline-block; width: 34px; height: 34px; border-radius: 50%;
    background: var(--white); flex: none;
  }

  /* Front side */
  .card-front { left: 500px; top: 480px; background: var(--white); }
  .band-top {
    position: absolute; left: 0; top: 0; width: 100%; height: 104px;
    background: var(--teal);
  }
  .band-bottom {
    position: absolute; left: 0; bottom: 0; width: 100%; height: 76px;
    background: var(--teal);
  }
  .person {
    position: absolute; left: 32px; top: 66px;
    color: var(--white); display: flex; align-items: baseline; gap: 10px;
  }
  .person-name {
    font-weight: 700; font-size: 17px; letter-spacing: .5px; text-transform: uppercase;
  }
  .person-divider { font-size: 17px; }
  .person-role { font-size: 14px; }
  .contacts {
    position: absolute; right: 30px; top: 16px;
    list-style: none; color: var(--white); font-size: 13px; line-height: 19px;
  }
  .contacts li { display: flex; align-items: center; gap: 7px; }
  .contacts svg { width: 10px; height: 10px; fill: var(--white); flex: none; }
  .front-brand {
    position: absolute; left: 0; right: 0; top: 140px;
    display: flex; justify-content: center; align-items: center; gap: 16px;
    color: var(--teal); font-size: 52px; letter-spacing: 3px; text-transform: uppercase;
    white-space: nowrap;
  }
  .front-brand .brand-dot { width: 40px; height: 40px; background: var(--teal); }
  .address {
    position: absolute; left: 0; right: 0; top: 236px;
    display: flex; justify-content: center; align-items: center; gap: 8px;
    color: var(--teal); font-size: 15px;
  }
  .address svg { width: 11px; height: 14px; fill: var(--teal); }
</style>
</head>
<body>

<section class="card card-back">
  <div class="pattern-area" role="img" aria-label="Repeating brand symbol pattern fading from bright blue to deep teal"></div>
  <div class="back-brand"><span class="brand-dot"></span><span>Maple Roster</span></div>
</section>

<section class="card card-front">
  <div class="band-top"></div>
  <div class="person">
    <span class="person-name">Dana Whitfield</span>
    <span class="person-divider">|</span>
    <span class="person-role">Director</span>
  </div>
  <ul class="contacts">
    <li><svg viewBox="0 0 10 10"><path d="M2 0.5l1.6 2-1 1.1a6 6 0 0 0 3.8 3.8l1.1-1 2 1.6-1 1.5C4.5 9.5.5 5.5.5 1.5z"/></svg>(555) 014-2290</li>
    <li><svg viewBox="0 0 10 10"><path d="M0 2h10v6H0zM1 3v.3l4 2.7 4-2.7V3zm0 1.5V7h8V4.5L5 7z"/></svg>info@mapleroster.com</li>
    <li><svg viewBox="0 0 10 10"><path d="M5 0a5 5 0 1 0 0 10A5 5 0 0 0 5 0zm0 1c.6.6 1 1.8 1.1 3.5H3.9C4 2.8 4.4 1.6 5 1zM1 5.5h1.9c.1 1.3.4 2.3.8 3A4 4 0 0 1 1 5.5zm0-1a4 4 0 0 1 2.7-3c-.4.7-.7 1.7-.8 3zm2.9 1h2.2C6 7.2 5.6 8.4 5 9c-.6-.6-1-1.8-1.1-3.5zm3.2 0H9a4 4 0 0 1-2.7 3c.4-.7.7-1.7.8-3zm0-1c-.1-1.3-.4-2.3-.8-3A4 4 0 0 1 9 4.5z"/></svg>www.mapleroster.com</li>
  </ul>
  <div class="front-brand"><span class="brand-dot"></span><span>Maple Roster</span></div>
  <div class="address">
    <svg viewBox="0 0 11 14"><path d="M5.5 0A5.5 5.5 0 0 0 0 5.5C0 9.5 5.5 14 5.5 14S11 9.5 11 5.5A5.5 5.5 0 0 0 5.5 0zm0 7.5a2 2 0 1 1 0-4 2 2 0 0 1 0 4z"/></svg>
    <span>418 Cedar Ridge Lane, Salem, OR 97302</span>
  </div>
  <div class="band-bottom"></div>
</section>

</body>
</html>
```